Web Design Project for SEARCH ENGINE !

We need a website design for torrents search engine.

The Website will be www.Qentrova.com

Qentrova is a a search engine for torrents.
Qentrova search and index torrents results from all torrents sites.

We will need:
Logo
WebSite Design
slogen (optional)

we need only PSDs - no codded pages are needed !

Design to the following screen Size & resolution: 1024 x 768

***PLEASE DOWNLOAD ATTACHED FILE !

```html
<!DOCTYPE html>
<html lang="en">
<head>
<meta charset="utf-8">
<title>Qentrova – torrents search engine</title>
<link rel="stylesheet" href="https://fonts.googleapis.com/css2?family=Questrial&family=Open+Sans:wght@400;700&display=swap">
<style>
:root{
  --green:#2db34a;
  --green-bright:#39c24f;
  --ink:#3a3a3a;
  --ink-soft:#555;
  --white:#fff;
}
*{margin:0;padding:0;box-sizing:border-box}
html,body{width:1200px;height:1036px;overflow:hidden;background:var(--white)}
a{text-decoration:none;color:inherit}
.page{position:relative;width:1200px;height:1036px;overflow:hidden;
  background:linear-gradient(#fff 0,#fff 780px,#ededed 960px,#e4e4e4 1036px);
  font-family:"Questrial",sans-serif;color:var(--ink)}
.abs{position:absolute}

/* brand */
.brand{left:33px;top:40px;display:flex;align-items:center;gap:6px;white-space:nowrap}
.brand-dot{width:40px;height:40px;border-radius:50%;background:var(--green);flex:none}
.brand-name{font-family:"Open Sans",sans-serif;font-weight:700;font-size:31px;color:var(--ink);letter-spacing:-1px;line-height:1}
.brand-sub{left:44px;top:86px;font-size:15.5px;color:var(--ink-soft);white-space:nowrap}

/* dark bars */
.dark-bar{background:linear-gradient(#3d3d3d,#141414);border-radius:10px;box-shadow:0 3px 5px rgba(0,0,0,.35)}
.nav{left:238px;top:14px;width:717px;height:66px;display:flex;align-items:center;padding-left:18px;
  font-size:17px;color:#fff;white-space:nowrap}
.nav a{color:#fff}
.nav a.active{color:var(--green-bright)}
.nav .sep{margin:0 9px;color:#ddd}
.lang{margin-left:16px;background:var(--green);color:#fff;font-size:14px;padding:4px 10px;border-radius:2px;display:flex;gap:12px}
.counter{left:998px;top:14px;width:147px;height:68px;text-align:center;color:#fff;white-space:nowrap}
.counter .label{font-size:12px;margin-top:8px;letter-spacing:.3px}
.counter .num{font-family:"Open Sans",sans-serif;font-weight:700;font-size:30px;letter-spacing:-1.5px;line-height:1.1}

.legal{left:258px;top:97px;font-size:11.6px;color:#444;white-space:nowrap}
.legal span{color:var(--green)}

/* hero */
.hero-frame{left:53px;top:138px;width:531px;height:277px;border-radius:32px;background:#c8c8c8;padding:8px;
  box-shadow:inset 0 0 0 1px #b5b5b5}
.hero-media{width:100%;height:100%;border-radius:25px;
  background:radial-gradient(ellipse at 45% 52%,#f3f6ff 0,#7fb0e0 14%,#2f5fa3 35%,#6b7c3a 60%,#8a5a32 80%,#2a2d3a 100%)}
.hero-panel{left:612px;top:138px;width:528px;height:277px;border-radius:32px;
  background:linear-gradient(#fff,#ececec);box-shadow:0 0 0 2px #ececec, inset 0 0 0 1px #e2e2e2;text-align:center;white-space:nowrap}
.hero-title{margin-top:40px;font-size:52px;font-weight:400;color:#444;line-height:1;letter-spacing:-.5px}
.hero-sub{font-size:30px;color:#444;margin-top:8px;line-height:1}
.hero-kinds{font-size:25px;color:var(--green);margin-top:10px}
.hero-cta{font-size:18px;color:#222;margin-top:10px}
.download{left:770px;top:359px;width:212px;height:65px;text-align:center;color:#fff;border-radius:6px;white-space:nowrap}
.download .small{font-size:17px;margin-top:6px}
.download .big{font-family:"Open Sans",sans-serif;font-weight:700;font-size:24px;line-height:1;display:flex;justify-content:center;align-items:center;gap:6px}
.download .big i{width:22px;height:22px;border-radius:50%;background:#fff;display:inline-block}
.tagline{left:0;width:1200px;top:446px;text-align:center;font-size:10.5px;color:#333;white-space:nowrap}

/* features */
.feature{top:490px;width:229px;height:272px;border-radius:22px 22px 0 0;
  background:linear-gradient(#f6f6f6,#dcdcdc);text-align:center;font-family:"Open Sans",sans-serif}
.feature svg{margin-top:14px}
.feature h2{font-size:25px;font-weight:700;color:#333;margin-top:4px;line-height:1.1}
.feature p{font-size:16px;color:#444;line-height:21px;margin-top:3px;padding:0 20px}
.ribbon{top:745px;width:248px;height:55px;color:#fff;font-size:17px;display:flex;align-items:center;justify-content:center;border-radius:6px}
.reflection{top:806px;width:248px;height:120px;overflow:hidden;opacity:.22;
  -webkit-mask-image:linear-gradient(#000,transparent);mask-image:linear-gradient(#000,transparent)}
.reflection .mirror{transform:scaleY(-1);height:40px;background:linear-gradient(#fff,#999);color:#000;font-size:17px;display:flex;align-items:center;justify-content:center;border-radius:6px}
.reflection .mirror-card{margin:4px auto 0;width:229px;height:80px;background:#ddd}

/* footer */
.social{left:301px;top:947px;width:600px;height:63px;display:flex;align-items:center;justify-content:center;gap:13px}
.social span{width:49px;height:42px;border-radius:3px;box-shadow:0 1px 2px rgba(0,0,0,.5)}
.contact{left:1035px;top:962px;display:flex;gap:8px}
</style>
</head>
<body>
<div class="page">

  <div class="abs brand"><span class="brand-dot"></span><span class="brand-name">Qentrova</span></div>
  <div class="abs brand-sub">torrents search engine</div>

  <nav class="abs nav dark-bar">
    <a class="active" href="#">HOME</a><span class="sep">|</span>
    <a href="#">ABOUT US</a><span class="sep">|</span>
    <a href="#">TORRENT SEARCH</a><span class="sep">|</span>
    <a href="#">SITE SEARCH</a><span class="sep">|</span>
    <a href="#">HELP</a><span class="sep">|</span>
    <a href="#">SIGNOUT</a>
    <span class="lang">English <span>▼</span></span>
  </nav>

  <div class="abs counter dark-bar">
    <div class="label">TORRENTS AVAILABLE</div>
    <div class="num">257.669</div>
  </div>

  <p class="abs legal">COPYRIGHT © 2011 QENTROVA. USE OF THIS WEBSITE CONSTITUTES ACCEPTANCE OF OUR <span>USER AGREEMENT</span> AND <span>PRIVACY POLICY</span>.</p>

  <div class="abs hero-frame"><div class="hero-media" role="img" aria-label="Tunnel of colourful media thumbnails streaming toward a bright centre"></div></div>

  <section class="abs hero-panel">
    <h1 class="hero-title">FIND,GET,ENJOY</h1>
    <div class="hero-sub">ALL KIND OF TORRENT FILES</div>
    <div class="hero-kinds">Movies, Games, Music, Software, etc.</div>
    <div class="hero-cta">GET OUR QENTROVA APP. AND START YOUR JOURNEY !</div>
  </section>
  <a class="abs download dark-bar" href="#"><div class="small">DOWNLOAD</div><div class="big"><i></i>Qentrova</div></a>

  <p class="abs tagline">QENTROVA IS A NEW LIGHTWEIGHT TORRENT SEARCH ENGINE, IT MAKES INCREDIBLY EFFICIENT USE OF NETWORK BANDWIDTH WHILE REDUCING NETWORK PROBLEMS.</p>

  <article class="abs feature" style="left:62px">
    <svg width="70" height="70" viewBox="0 0 70 70" aria-hidden="true"><g fill="var(--green)"><rect x="8" y="38" width="40" height="10" rx="2" transform="rotate(-45 28 43)"/><g stroke="var(--green)" stroke-width="4" stroke-linecap="round"><line x1="48" y1="6" x2="48" y2="14"/><line x1="62" y1="20" x2="54" y2="20"/><line x1="38" y1="10" x2="42" y2="15"/><line x1="58" y1="9" x2="54" y2="13"/><line x1="58" y1="31" x2="54" y2="27"/></g></g></svg>
    <h2>Easy</h2>
    <p>Simple and straightforward – that's Qentrova. With its purpose-built interface, downloading torrents is a snap.</p>
  </article>
  <article class="abs feature" style="left:343px">
    <svg width="70" height="70" viewBox="0 0 70 70" aria-hidden="true"><g fill="var(--green)"><rect x="30" y="4" width="10" height="28" rx="2" transform="rotate(-20 35 18)"/><path d="M22 30a18 18 0 1 0 26 26h-8a11 11 0 1 1-14-18z"/><rect x="18" y="58" width="40" height="8" rx="2"/><rect x="36" y="38" width="14" height="6"/></g></svg>
    <h2>Tiny</h2>
    <p>It installs ultra-fast with a light footprint on your computer, and runs super-efficiently.</p>
  </article>
  <article class="abs feature" style="left:625px">
    <svg width="70" height="70" viewBox="0 0 70 70" aria-hidden="true"><path d="M35 10a30 30 0 0 0-30 30v10a5 5 0 0 0 5 5h50a5 5 0 0 0 5-5V40a30 30 0 0 0-30-30z" fill="var(--green)"/><path d="M35 44 46 22" stroke="#fff" stroke-width="4" stroke-linecap="round"/><circle cx="35" cy="44" r="4" fill="#fff"/><g stroke="#fff" stroke-width="3"><line x1="14" y1="40" x2="19" y2="40"/><line x1="51" y1="40" x2="56" y2="40"/><line x1="35" y1="18" x2="35" y2="23"/><line x1="20" y1="25" x2="23.5" y2="28.5"/></g></svg>
    <h2>Fast</h2>
    <p>Expertly designed for fast downloads. Avoids hogging valuable system resources, runs quietly in the background.</p>
  </article>
  <article class="abs feature" style="left:905px">
    <svg width="70" height="70" viewBox="0 0 70 70" aria-hidden="true"><circle cx="35" cy="38" r="28" fill="var(--green)"/></svg>
    <h2>Accessible</h2>
    <p>Access from anywhere with Qentrova App. Easily access your home clients privately and securely.</p>
  </article>

  <a class="abs ribbon dark-bar" style="left:53px" href="#">READ MORE</a>
  <a class="abs ribbon dark-bar" style="left:334px" href="#">READ MORE</a>
  <a class="abs ribbon dark-bar" style="left:615px" href="#">READ MORE</a>
  <a class="abs ribbon dark-bar" style="left:896px" href="#">READ MORE</a>

  <div class="abs reflection" style="left:53px" aria-hidden="true"><div class="mirror">READ MORE</div><div class="mirror-card"></div></div>
  <div class="abs reflection" style="left:334px" aria-hidden="true"><div class="mirror">READ MORE</div><div class="mirror-card"></div></div>
  <div class="abs reflection" style="left:615px" aria-hidden="true"><div class="mirror">READ MORE</div><div class="mirror-card"></div></div>
  <div class="abs reflection" style="left:896px" aria-hidden="true"><div class="mirror">READ MORE</div><div class="mirror-card"></div></div>

  <footer class="abs social dark-bar" aria-label="Social links">
    <span style="background:#e8e8e8"></span>
    <span style="background:#e67a2e"></span>
    <span style="background:#8ec6dc"></span>
    <span style="background:#3b65a8"></span>
    <span style="background:#1e6a7a"></span>
    <span style="background:#e0e0e8"></span>
    <span style="background:#2a2a6a"></span>
    <span style="background:#c8c24a"></span>
    <span style="background:#2a86c8"></span>
  </footer>

  <div class="abs contact" aria-label="Contact shortcuts">
    <svg width="22" height="22" viewBox="0 0 22 22" aria-label="Account"><circle cx="11" cy="6" r="5" fill="#333"/><path d="M2 22a9 8 0 0 1 18 0z" fill="#333"/></svg>
    <svg width="26" height="22" viewBox="0 0 26 22" aria-label="Home"><path d="M13 1 1 12h4v9h6v-6h4v6h6v-9h4z" fill="#333"/></svg>
    <svg width="24" height="22" viewBox="0 0 24 22" aria-label="Phone"><path d="M3 3c3-3 5-2 6 1l-2 3c1 3 4 6 7 7l3-2c3 1 4 3 1 6-4 4-19-11-15-15z" fill="#333"/></svg>
    <svg width="24" height="22" viewBox="0 0 24 22" aria-label="Email"><rect x="1.5" y="4.5" width="21" height="14" fill="none" stroke="#333" stroke-width="2"/><path d="M1.5 4.5 12 13l10.5-8.5" fill="none" stroke="#333" stroke-width="2"/></svg>
  </div>

</div>
</body>
</html>
```